Company or website name
- Quiet Hollow Properties
- Describe your company and organization and target audience
- We sell rural vacant, mostly residential land. Our target market is looking for privacy and either a place to retire to or a place to escape to.
- The design should have the following
- Mountains, Pine Trees, Earthy Colors, and match the attached logo. The home page should have designs for slides of properties at the top, followed by a survey (for users to share details of the property they're looking for), followed by search functionality, individual properties and general areas properties are available in. We'll also need at least one contact form on each page as well as maps. For the property detail page we'll need a large area for pictures, highlighted property details, a description and more detailed facts about property. The property detail page should also have a survey for users to share details of what they're looking for and contact form. Last but not least, similar properties should also be included on the property listing page. The winning design will include an excellent "Contact Us" page! Every page should have an opt-in offering users to be notified when new properties become available.
- Briefly describe your contest

```html
<!DOCTYPE html>
<html lang="en">
<head>
<meta charset="utf-8">
<title>Quiet Hollow Properties — Home</title>
<link href="https://fonts.googleapis.com/css2?family=Noto+Serif:wght@400;700&family=Open+Sans:ital,wght@0,400;0,600;0,700;1,400&family=Montserrat:wght@400;500;600&display=swap" rel="stylesheet">
<style>
:root{
  --forest:#185e4e;
  --forest-dark:#114a3d;
  --mint:#a9d2ce;
  --mint-ink:#7fb3ad;
  --ink:#222;
  --nav-bg:#f3f3f3;
  --white:#fff;
}
*{box-sizing:border-box;margin:0;padding:0}
html,body{width:1200px;height:2961px;overflow:hidden;background:#fff}
body{font-family:"Open Sans",sans-serif;color:var(--ink)}
.canvas{position:relative;width:1200px;height:2961px;overflow:hidden}
.abs{position:absolute}
a{color:inherit;text-decoration:none}

.topbar{left:0;top:0;width:1200px;height:38px;background:var(--forest);color:#fff;font-size:10px}
.topbar .item{position:absolute;top:12px;display:flex;align-items:center;gap:7px}
.topbar .dot{width:13px;height:13px;border-radius:50%;background:#6aa6e0}
.topbar .dot.orange{background:#f2a43a}

.nav{left:0;top:38px;width:1200px;height:62px;background:var(--nav-bg)}
.brand{position:absolute;left:34px;top:14px;display:flex;align-items:center;gap:6px;font-family:"Montserrat",sans-serif;font-weight:600;font-size:11px;color:var(--forest);line-height:1.1;width:140px}
.brand .mark{width:34px;height:34px;border-radius:50%;background:var(--forest);flex:none}
.nav .link{position:absolute;top:25px;font-family:"Montserrat",sans-serif;font-size:11px;letter-spacing:1.3px;color:#333}
.nav .link.active{color:var(--forest)}

.hero{left:0;top:100px;width:1200px;height:575px;background:linear-gradient(180deg,#5d615c 0%,#4a5048 35%,#2f3a33 60%,#1f2b26 80%,#3a3128 100%)}
.hero h1{position:absolute;left:0;width:1200px;top:181px;text-align:center;font-family:"Noto Serif",serif;font-weight:400;font-size:29px;letter-spacing:6px;color:#fff;line-height:38px}
.hero .sub{position:absolute;left:0;width:1200px;top:222px;text-align:center;font-size:12px;color:#fff;line-height:18px}
.field{position:absolute;background:#fff;border-radius:4px;color:#999;font-size:15px;display:flex;align-items:center;padding:0 11px}
.field svg{position:absolute;right:12px}
.hero-arrow{position:absolute;top:255px}

.h2{position:absolute;font-family:"Noto Serif",serif;font-weight:400;font-size:19px;letter-spacing:4px;color:var(--forest)}
.btn-outline{position:absolute;border:1.5px solid var(--forest);color:var(--forest);font-size:13px;display:flex;align-items:center;justify-content:center}

.explore-card{position:absolute;top:763px;width:251px;height:240px;background:#fff;box-shadow:0 0 5px rgba(0,0,0,.25);text-align:center}
.explore-card .photo{position:absolute;left:63px;top:17px;width:125px;height:125px;border-radius:50%}
.explore-card h3{position:absolute;left:0;width:100%;top:153px;font-size:13px;font-weight:600}
.explore-card p{position:absolute;left:26px;width:199px;top:175px;font-size:8.5px;line-height:1.3}
.explore-card .cta{position:absolute;left:0;width:100%;top:210px;font-size:11.5px;font-weight:700;text-decoration:underline}

.prop{position:absolute;top:1108px;width:251px;height:189px;background:#fff;box-shadow:0 0 5px rgba(0,0,0,.25)}
.prop .photo{position:absolute;left:0;top:0;width:251px;height:156px;background:linear-gradient(180deg,#b9c9c9 0%,#8e9a93 45%,#5f7d48 75%,#6d9a3c 100%)}
.prop .price{position:absolute;left:13px;top:167px;font-family:"Montserrat",sans-serif;font-weight:600;font-size:12px;letter-spacing:2px}
.prop .loc{position:absolute;right:13px;top:166px;font-size:12px;color:#444;display:flex;gap:4px;align-items:center}
.prop .facts{position:absolute;left:0;top:130px;width:251px;height:26px;display:flex;align-items:center;justify-content:space-around;font-family:"Noto Serif",serif;font-size:8.5px;letter-spacing:1.5px;color:#fff;background:linear-gradient(180deg,rgba(24,94,78,0),rgba(24,94,78,.55))}
.circle-arrow{position:absolute;width:31px;height:31px;border-radius:50%;background:#555;display:flex;align-items:center;justify-content:center}

.community{position:absolute;top:1411px;height:187px}
.community .label{position:absolute;left:0;bottom:0;width:100%;height:37px;background:rgba(24,94,78,.85);color:#fff;font-size:13.5px;display:flex;align-items:center;justify-content:center}

.testi{position:absolute;top:1715px;height:210px;background:var(--mint);color:var(--mint-ink)}
.testi.active{background:#fff;color:var(--ink);box-shadow:0 0 6px rgba(0,0,0,.3)}
.testi .quote{position:absolute;left:18px;top:0;width:22px;height:22px;background:var(--mint-ink);color:#fff;font-family:"Noto Serif",serif;font-weight:700;font-size:16px;text-align:center;line-height:26px}
.testi.active .quote{background:var(--mint)}
.testi p{position:absolute;left:18px;right:18px;top:53px;font-size:10.3px;line-height:22.5px}
.testi .name{position:absolute;left:18px;top:139px;font-family:"Montserrat",sans-serif;font-size:12px;letter-spacing:2px}
.testi .role{position:absolute;left:18px;top:166px;font-size:8.5px}
.testi.active .role{color:#333}

.blog-main{left:32px;top:2039px;width:765px;height:537px;background:linear-gradient(180deg,#4b4e4a 0%,#6a6e69 30%,#3d4a42 55%,#2a3831 75%,#2b2a24 100%)}
.blog-main .inner{position:absolute;left:140px;width:485px;top:200px;text-align:center;color:#fff}
.blog-main .date{font-size:9.5px;font-style:italic}
.blog-main h3{font-family:"Montserrat",sans-serif;font-weight:500;font-size:12.5px;letter-spacing:1.5px;margin-top:12px}
.blog-main p{font-size:9px;line-height:17.5px;margin-top:12px}
.blog-side{position:absolute;left:832px;width:330px}
.blog-side .photo{height:155px}
.blog-side .date{font-size:8.5px;font-style:italic;margin-top:11px}
.blog-side h4{font-family:"Montserrat",sans-serif;font-weight:500;font-size:12.5px;letter-spacing:1.2px;line-height:19px;margin-top:4px}
.blog-side p{font-size:8.8px;line-height:17px;color:#555;margin-top:6px}

.footer{left:0;top:2638px;width:1200px;height:286px;background:var(--forest);color:#fff}
.footer .label{position:absolute;font-family:"Montserrat",sans-serif;font-size:9px;letter-spacing:1.8px}
.footer .small{position:absolute;font-size:9px;line-height:17px}
.footer .links a{display:block;font-size:9px;height:22.5px}
.footer .input{position:absolute;left:734px;width:232px;border-bottom:1px solid #fff;background:var(--forest-dark);font-size:7.5px;padding:10px 6px;color:#fff}
.footer .send{position:absolute;left:734px;width:100px;height:31px;border:1.5px solid #fff;font-family:"Montserrat",sans-serif;font-size:10px;letter-spacing:2px;display:flex;align-items:center;justify-content:center}
.copyright{left:0;top:2924px;width:1200px;height:37px;background:var(--forest-dark);color:#fff;font-size:9px;display:flex;align-items:center;justify-content:center}
</style>
</head>
<body>
<div class="canvas">

  <div class="abs topbar">
    <div class="item" style="left:36px"><span class="dot"></span>info@quiethollowproperties.com</div>
    <div class="item" style="left:214px"><span class="dot orange"></span>+1 555 010 2345</div>
    <div class="item" style="left:1087px"><span class="dot orange"></span>Login &nbsp;/&nbsp; Signup</div>
  </div>

  <header class="abs nav">
    <div class="brand"><span class="mark"></span>Quiet Hollow Properties</div>
    <a class="link active" style="left:672px">HOME</a>
    <a class="link" style="left:753px">PROPERTIES</a>
    <a class="link" style="left:871px">ABOUT US</a>
    <a class="link" style="left:976px">CONTACT</a>
    <a class="link" style="left:1075px">BLOG</a>
    <svg class="abs" style="left:1144px;top:22px" width="18" height="18" viewBox="0 0 18 18" fill="none" stroke="#333" stroke-width="1.6"><circle cx="7.5" cy="7.5" r="6"/><path d="M12 12l5 5"/></svg>
  </header>

  <section class="abs hero" role="img" aria-label="Mountain lake with pine forest and wooden boathouse">
    <h1>WHAT ARE YOU LOOKING FOR?</h1>
    <p class="sub">No matter what your property needs, Quiet Hollow Properties is here for you</p>
    <svg class="hero-arrow" style="left:34px" width="14" height="24" viewBox="0 0 14 24" fill="none" stroke="#fff" stroke-width="1.5"><path d="M12 2L2 12l10 10"/></svg>
    <svg class="hero-arrow" style="left:1142px;top:252px" width="14" height="24" viewBox="0 0 14 24" fill="none" stroke="#fff" stroke-width="1.5"><path d="M2 2l10 10L2 22"/></svg>
    <div class="field" style="left:335px;top:273px;width:126px;height:43px">Buy / Sell<svg width="18" height="10" viewBox="0 0 18 10" fill="none" stroke="#666" stroke-width="1.5"><path d="M1 1l8 8 8-8"/></svg></div>
    <div class="field" style="left:476px;top:273px;width:187px;height:43px">Type of property<svg width="18" height="10" viewBox="0 0 18 10" fill="none" stroke="#666" stroke-width="1.5"><path d="M1 1l8 8 8-8"/></svg></div>
    <div class="field" style="left:678px;top:273px;width:94px;height:43px;border-radius:4px 0 0 4px;border-right:1px solid #ddd">$ Min</div>
    <div class="field" style="left:772px;top:273px;width:93px;height:43px;border-radius:0 4px 4px 0">$ Max</div>
    <div class="field" style="left:335px;top:330px;width:530px;height:48px">Enter an address, neigborhood, city or ZIP code<svg width="28" height="28" viewBox="0 0 28 28" fill="none" stroke="#185e4e" stroke-width="2.5"><circle cx="12" cy="12" r="10"/><path d="M19.5 19.5l6 6"/></svg></div>
  </section>

  <svg class="abs" style="left:560px;top:702px" width="84" height="14" viewBox="0 0 84 14" fill="none">
    <path d="M8 2l5 5-5 5-5-5z" stroke="#222" stroke-width="1.5"/>
    <path d="M40 3l4 4-4 4-4-4z" stroke="#777"/><circle cx="40" cy="7" r="1.3" fill="#777"/>
    <path d="M72 3l4 4-4 4-4-4z" stroke="#777"/><circle cx="72" cy="7" r="1.3" fill="#777"/>
  </svg>

  <h2 class="h2" style="left:180px;top:715px">EXPLORE ALL THINGS PROPERTY</h2>
  <div class="explore-card" style="left:182px">
    <div class="photo" role="img" aria-label="City skyline of tall buildings" style="background:linear-gradient(180deg,#c9c9c9,#6a6865 60%,#4a3b30)"></div>
    <h3>Explore neighborhood profile</h3>
    <p>Check out diffrent neighbourhoods and find one that's &nbsp;right for you</p>
    <a class="cta">Explore neighborhoods</a>
  </div>
  <div class="explore-card" style="left:476px">
    <div class="photo" role="img" aria-label="Two people reviewing plans on a laptop" style="background:linear-gradient(180deg,#8a9498,#4b4a4c 55%,#7a2a2a)"></div>
    <h3 style="top:156px">Need help about your concern?</h3>
    <p style="top:176px">Wondering about the right place, procedures, loans, mortgages... We are here for you.</p>
    <a class="cta">Contact us</a>
  </div>
  <div class="explore-card" style="left:769px">
    <div class="photo" role="img" aria-label="Small house model on blueprints" style="background:linear-gradient(180deg,#d9d9d9,#9aa1a3 45%,#b33 60%,#e2e2e2)"></div>
    <h3>Get latest property news and advice</h3>
    <p style="top:178px">Subscribe to the latest property news.</p>
    <a class="cta">Subscribe</a>
  </div>

  <h2 class="h2" style="left:180px;top:1061px">FEATURED PROPERTIES</h2>
  <a class="btn-outline" style="left:848px;top:1064px;width:170px;height:24px">View our properties</a>
  <div class="circle-arrow" style="left:103px;top:1179px"><svg width="10" height="14" viewBox="0 0 10 14" fill="none" stroke="#fff" stroke-width="2"><path d="M8 1L2 7l6 6"/></svg></div>
  <div class="circle-arrow" style="left:1065px;top:1194px"><svg width="10" height="14" viewBox="0 0 10 14" fill="none" stroke="#fff" stroke-width="2"><path d="M2 1l6 6-6 6"/></svg></div>

  <article class="prop" style="left:182px">
    <div class="photo" role="img" aria-label="White farmhouse with wraparound porch and lawn"></div>
    <span class="price">$500.000</span>
    <span class="loc"><svg width="9" height="12" viewBox="0 0 9 12" fill="none" stroke="#555"><path d="M4.5 11S1 7 1 4.5a3.5 3.5 0 017 0C8 7 4.5 11 4.5 11z"/><circle cx="4.5" cy="4.5" r="1.3"/></svg>Birch Hollow</span>
  </article>
  <article class="prop" style="left:479px">
    <div class="photo" role="img" aria-label="White farmhouse with wraparound porch and lawn"></div>
    <div class="facts"><span>BEDS: 4</span><span>BATHS: 4</span><span>SIZE: 1200 M2</span></div>
    <span class="price">$500.000</span>
    <span class="loc"><svg width="9" height="12" viewBox="0 0 9 12" fill="none" stroke="#555"><path d="M4.5 11S1 7 1 4.5a3.5 3.5 0 017 0C8 7 4.5 11 4.5 11z"/><circle cx="4.5" cy="4.5" r="1.3"/></svg>Birch Hollow</span>
  </article>
  <article class="prop" style="left:766px">
    <div class="photo" role="img" aria-label="White farmhouse with wraparound porch and lawn"></div>
    <span class="price">$500.000</span>
    <span class="loc"><svg width="9" height="12" viewBox="0 0 9 12" fill="none" stroke="#555"><path d="M4.5 11S1 7 1 4.5a3.5 3.5 0 017 0C8 7 4.5 11 4.5 11z"/><circle cx="4.5" cy="4.5" r="1.3"/></svg>Birch Hollow</span>
  </article>

  <h2 class="h2" style="left:180px;top:1363px">AVAILABLE COMMUNITIES</h2>
  <a class="btn-outline" style="left:799px;top:1366px;width:220px;height:24px">View available Communities</a>
  <div class="community" role="img" aria-label="Tree-lined residential street at sunset" style="left:0;width:215px;background:linear-gradient(180deg,#e9ddd6,#cdbcae 60%,#e0dad6)"></div>
  <div class="community" role="img" aria-label="Cream multi-storey homes with balconies" style="left:234px;width:231px;background:linear-gradient(180deg,#b9d2e6,#d9cdb4 40%,#a9a18c 80%,#6f8a4f)"></div>
  <div class="community" role="img" aria-label="Red two-storey house with front lawn" style="left:485px;width:230px;background:linear-gradient(180deg,#b5cfe3,#a84b3b 35%,#8d6f5a 60%,#6e9b3f)"><div class="label">Cedar Flats</div></div>
  <div class="community" role="img" aria-label="Brownstone row houses with iron fence" style="left:734px;width:231px;background:linear-gradient(180deg,#d9d6d2,#6b4a3a 40%,#3e4a32 75%,#2e3b28)"></div>
  <div class="community" role="img" aria-label="Suburban houses beside a pond" style="left:985px;width:215px;background:linear-gradient(180deg,#e3ecf4,#d8dde0 55%,#c9d3d4)"></div>
  <svg class="abs" style="left:34px;top:1481px" width="14" height="24" viewBox="0 0 14 24" fill="none" stroke="#333" stroke-width="1.5"><path d="M12 2L2 12l10 10"/></svg>
  <svg class="abs" style="left:1142px;top:1478px" width="14" height="24" viewBox="0 0 14 24" fill="none" stroke="#333" stroke-width="1.5"><path d="M2 2l10 10L2 22"/></svg>

  <h2 class="h2" style="left:180px;top:1667px">TESTIMONIALS</h2>
  <a class="btn-outline" style="left:769px;top:1671px;width:250px;height:24px">Read more client testimonials</a>
  <div class="testi" style="left:0;width:219px;overflow:hidden">
    <p style="left:-6px;right:8px;white-space:nowrap;overflow:hidden">met, consectetur adipiscing elit, sed do<br>unt ut labore et dolore magna aliqua. Ut</p>
  </div>
  <div class="testi active" style="left:238px;width:356px">
    <div class="quote">&ldquo;</div>
    <p>Lorem ipsum dolor sit amet, consectetur adipiscing elit, sed do eiusmod tempor incididunt ut labore et dolore magna aliqua. Ut enim ad minim veniam.</p>
    <div class="name">MARA LINDEN</div>
    <div class="role">Happy Client</div>
  </div>
  <div class="testi" style="left:614px;width:355px">
    <div class="quote">&ldquo;</div>
    <p>Lorem ipsum dolor sit amet, consectetur adipiscing elit, sed do eiusmod tempor incididunt ut labore et dolore magna aliqua. Ut enim ad minim veniam.</p>
    <div class="name">OWEN</div>
    <div class="role">Happy Client</div>
  </div>
  <div class="testi" style="left:988px;width:212px;overflow:hidden">
    <div class="quote">&ldquo;</div>
    <p style="right:auto;width:340px">Lorem ipsum dolor sit amet, consectetur adipiscing elit, sed do eiusmod tempor incididunt ut labore et dolore magna aliqua. Ut enim ad minim veniam.</p>
    <div class="name">OWEN</div>
    <div class="role">Happy Client</div>
  </div>
  <svg class="abs" style="left:34px;top:1810px" width="14" height="24" viewBox="0 0 14 24" fill="none" stroke="#333" stroke-width="1.5"><path d="M12 2L2 12l10 10"/></svg>
  <svg class="abs" style="left:1142px;top:1807px" width="14" height="24" viewBox="0 0 14 24" fill="none" stroke="#333" stroke-width="1.5"><path d="M2 2l10 10L2 22"/></svg>

  <h2 class="h2" style="left:180px;top:1990px;letter-spacing:1.5px">LASTEST FROM OUR BLOG</h2>
  <article class="abs blog-main" role="img" aria-label="Misty mountain lake with boathouse">
    <div class="inner">
      <div class="date">March 22, 2022</div>
      <h3>Lorem ipsum dolor sit amet, consectetur adipiscing elit</h3>
      <p>&ldquo;Sed do eiusmod tempor incididunt ut labore et dolore magna aliqua. Ut enim ad minim veniam, quis nostrud exercitation ullamco laboris nisi ut aliquip ex ea commodo consequat. Duis aute irure dolor in reprehenderit in voluptate velit esse cillum dolore eu fugiat nulla pariatur. Excepteur sint occaecat cupidatat non proident, sunt in culpa qui officia deserunt mollit anim id est laborum...&rdquo;</p>
    </div>
  </article>
  <article class="blog-side" style="top:2039px">
    <div class="photo" role="img" aria-label="Brick house with double garage in autumn" style="background:linear-gradient(180deg,#b8cde0,#8a6a55 45%,#9a8c7c 75%,#9b9b96)"></div>
    <div class="date">March 22, 2022</div>
    <h4>Lorem ipsum dolor sit amet, consectetur adipiscing elit</h4>
    <p>Sed do eiusmod tempor incididunt ut labore et dolore magna aliqua. Ut enim ad minim veniam, quis nostrud exercitation ullamco laboris nisi...</p>
  </article>
  <article class="blog-side" style="top:2324px">
    <div class="photo" role="img" aria-label="White farmhouse with porch and lawn" style="height:156px;background:linear-gradient(180deg,#b9c9c9,#8e9a93 45%,#5f7d48 75%,#6d9a3c)"></div>
    <div class="date" style="margin-top:8px">August 27, 2015</div>
    <h4>Lorem ipsum dolor sit amet, consectetur adipiscing elit</h4>
    <p>Sed do eiusmod tempor incididunt ut labore et dolore magna aliqua. Ut enim ad minim veniam, quis nostrud exercitation ullamco laboris nisi...</p>
  </article>

  <footer class="abs footer">
    <div class="abs" style="left:236px;top:38px;display:flex;align-items:center;gap:6px;width:200px;font-family:'Montserrat',sans-serif;font-weight:600;font-size:11px">
      <span style="width:36px;height:36px;border-radius:50%;background:#fff;flex:none"></span>Quiet Hollow Properties
    </div>
    <div class="label" style="left:234px;top:104px;font-size:10px;letter-spacing:1px">CONTACT US</div>
    <div class="small" style="left:234px;top:120px">Phone number: +1 555 010 2345<br>Email: info@quiethollowproperties.com<br>Address: 418 Alder Ridge Road, Fernvale</div>

    <div class="label" style="left:483px;top:39px">SEARCH PROPERTY</div>
    <nav class="abs links" style="left:483px;top:68px">
      <a>Home for sale in Indiana</a>
      <a>Home for sale in Maine</a>
      <a>Home for sale in Massachusetts</a>
      <a>Home for sale in Montana</a>
      <a>Home for sale in South Carolina</a>
    </nav>

    <div class="label" style="left:734px;top:39px">WE WOULD LOVE TO HEAR FROM YOU</div>
    <div class="input" style="top:59px;height:30px">Name</div>
    <div class="input" style="top:97px;height:30px">Email</div>
    <div class="input" style="top:134px;height:66px;padding-top:16px">Message</div>
    <div class="send" style="top:216px">SEND</div>
  </footer>

  <div class="abs copyright">Copyright © 2022 QuietHollowProperties- All Rights Reserved</div>
</div>
</body>
</html>
```